Design a New Business Card for Our Company

We are looking for fresh, unique, and a modern business card that reflects our roots as digital marketing agency focused on SEM.

Industry/Entity Type

Marketing

Contact Information for Business Card

looking for very unique out of the box designs. clean and modern that compliments our logo

Requirements
Must have
• colors should match our logo
• Front should have name, address, email, and phone/fax of the person, phone/fax are the same number
• back should have our url

```html
<!DOCTYPE html>
<html lang="en">
<head>
<meta charset="utf-8">
<title>Brightway Media – Business Card</title>
<link rel="stylesheet" href="https://fonts.googleapis.com/css2?family=Source+Sans+3:wght@400;600;700&display=swap">
<style>
  :root {
    --stage: #e9e7e3;
    --brand-blue: #5b97d1;
    --accent-blue: #3f86cf;
    --ink: #2b2b2b;
    --muted: #9a9a9a;
    --paper: #ffffff;
    --faint-dot: #eceef4;
    --shadow: rgba(0, 0, 0, 0.18);
  }
  * { box-sizing: border-box; margin: 0; padding: 0; }
  html, body {
    width: 1200px;
    height: 675px;
    overflow: hidden;
    background: var(--stage);
    font-family: "Source Sans 3", "Helvetica Neue", Arial, sans-serif;
  }
  .canvas {
    position: relative;
    width: 1200px;
    height: 675px;
    display: flex;
    align-items: center;
    justify-content: center;
    gap: 48px;
  }
  .card {
    position: relative;
    width: 520px;
    height: 297px;
    border-radius: 2px;
    box-shadow: 0 10px 24px var(--shadow);
    overflow: hidden;
  }

  /* Back of card */
  .card--back {
    background: var(--brand-blue);
    color: var(--paper);
  }
  .card--back .wordmark {
    position: absolute;
    left: 112px;
    top: 102px;
    display: flex;
    align-items: center;
    gap: 12px;
    font-size: 46px;
    font-weight: 700;
    letter-spacing: -0.5px;
    color: var(--paper);
  }
  .card--back .wordmark__dot {
    width: 30px; height: 30px;
    border-radius: 50%;
    background: var(--paper);
  }
  .card--back .url {
    position: absolute;
    left: 136px;
    top: 220px;
    font-size: 14px;
    letter-spacing: 0.2px;
  }

  /* Front of card */
  .card--front {
    background: var(--paper);
    color: var(--ink);
  }
  .card--front .wordmark {
    position: absolute;
    left: 34px;
    top: 30px;
    display: flex;
    align-items: center;
    gap: 10px;
    font-size: 34px;
    font-weight: 700;
    letter-spacing: -0.4px;
    color: var(--accent-blue);
  }
  .card--front .wordmark__dot {
    width: 22px; height: 22px;
    border-radius: 50%;
    background: var(--accent-blue);
  }
  .backdrop-circle {
    position: absolute;
    right: -40px;
    top: 100px;
    width: 260px;
    height: 260px;
    border-radius: 50%;
    background: var(--faint-dot);
  }
  .contact {
    position: absolute;
    left: 34px;
    top: 128px;
    font-size: 14px;
    line-height: 19px;
  }
  .contact__address { margin-bottom: 4px; }
  .contact__list { list-style: none; }
  .contact__item {
    display: flex;
    align-items: center;
    gap: 8px;
  }
  .contact__icon { width: 13px; height: 13px; flex: none; }
  .person {
    position: absolute;
    right: 44px;
    top: 186px;
    text-align: right;
    z-index: 1;
  }
  .person__name {
    font-size: 20px;
    font-weight: 700;
    color: var(--accent-blue);
  }
  .person__title {
    font-size: 14px;
    color: var(--muted);
  }
</style>
</head>
<body>
<main class="canvas">

  <section class="card card--back" aria-label="Card back">
    <div class="wordmark">
      <span class="wordmark__dot"></span>
      <span class="wordmark__name">Brightway Media</span>
    </div>
    <p class="url">www.brightwaymedia.com</p>
  </section>

  <section class="card card--front" aria-label="Card front">
    <div class="backdrop-circle" aria-hidden="true"></div>

    <div class="wordmark">
      <span class="wordmark__dot"></span>
      <span class="wordmark__name">Brightway Media</span>
    </div>

    <address class="contact" style="font-style:normal">
      <p class="contact__address">48 Cedar Lane, Suite 210,<br>Boise, ID 83702</p>
      <ul class="contact__list">
        <li class="contact__item">
          <svg class="contact__icon" viewBox="0 0 16 16" aria-label="Phone"><path fill="var(--accent-blue)" d="M4 1.5l2.3 2.8-1.2 1.6c.8 1.8 2.2 3.2 4 4l1.6-1.2 2.8 2.3-1.2 2.5C7 13.2 2.8 9 1.5 3.2z"/></svg>
          <span>555.210.4400</span>
        </li>
        <li class="contact__item">
          <svg class="contact__icon" viewBox="0 0 16 16" aria-label="Fax"><rect x="4" y="1.5" width="8" height="4" fill="none" stroke="var(--accent-blue)" stroke-width="1.5"/><rect x="1.5" y="6" width="13" height="6" rx="1" fill="var(--accent-blue)"/><rect x="4" y="10" width="8" height="4.5" fill="var(--paper)" stroke="var(--accent-blue)" stroke-width="1.5"/></svg>
          <span>555.210.4400</span>
        </li>
        <li class="contact__item">
          <svg class="contact__icon" viewBox="0 0 16 16" aria-label="Email"><rect x="1" y="3" width="14" height="10" rx="1" fill="var(--accent-blue)"/><path d="M1.5 3.6L8 9l6.5-5.4" fill="none" stroke="var(--paper)" stroke-width="1.3"/></svg>
          <span>hello@brightwaymedia.com</span>
        </li>
        <li class="contact__item">
          <svg class="contact__icon" viewBox="0 0 16 16" aria-label="Website"><g fill="none" stroke="var(--accent-blue)" stroke-width="1.3"><circle cx="8" cy="8" r="6.5"/><ellipse cx="8" cy="8" rx="3" ry="6.5"/><path d="M1.5 8h13M2.6 4.5h10.8M2.6 11.5h10.8"/></g></svg>
          <span>www.brightwaymedia.com</span>
        </li>
      </ul>
    </address>

    <div class="person">
      <p class="person__name">Dana Whitfield</p>
      <p class="person__title">Owner</p>
    </div>
  </section>

</main>
</body>
</html>
```